Packaging and Insert Design for New Cocktail/Bar Set

We are launching a new product under our brand, Shaker Haven, and require a design for the product packaging (2 packages - an inner cylinder tube and an outer box), as well as an insert.

(Note for reference - "mixology" is the art of cocktail making).

Our product is a cocktail set which will be sold on the USA Amazon site.

Our logo has already been designed - please refer to the attached files. I've attached various vector files of our logo.

The cocktail set will be packaged in a cylinder tube box.
Please see uploaded files for an image of the cylinder, as well as dimensions.
Dimensions are 37.68cm x 28cm (when the print design is laid flat).
The physical tube will be 28cm high and have a diameter of 12cm.
See uploaded file 'Dimensions - Cylinder Box' for details.

The cylinder box will be enclosed in an outer white box for protection. The outer white box will be a very basic box (i.e. not high quality) we are using just to make storage of individual units easier (and to protect the cylinder tube). It is unlikely that the outer box will be retained by the buyer. It will have a very clean, simple design. It will have our logo on the front and a barcode on the back (at the bottom).
Dimensions of the outer box are 28.5cm high and 12.5cm wide (tall and rectangular in shape).
See uploaded file 'Dimensions - White Outer Box & Paper Card' for details.

So to confirm we have 2 packages - the internal cylinder tube will have full branding, and this will then be placed in the white outer box with a simple design (logo only plus barcode at the back).

We also require a small insert to be designed (9.1cm x 5.5cm). We will include the insert in the package. The insert will have our logo and will provide the buyer with our contact details. The buyer will register their email address with us, in order to quality for warranty and a free e-book.

We need to finalise the content for the product insert, as well as the additional information to be printed on the cylinder tube.

In terms of design for the inner cylinder tube, we are leaning towards a more simple design, with our logo displayed on the front of the box.
We are open to ideas/suggestions though.

We have also uploaded an image of the cocktail set components which will form part of the set.

Target Market(s)

Our target market will be cocktail making enthusiasts/hobbyists and professionals. This includes people who would like to but a cocktail set to use at home, as well as professional bartenders.

Industry/Entity Type

Product

Colors

Designer to choose colors to be used in the design.

Requirements
Must have
• Preference is for a clean, professional looking design.
• Internal cylinder tube - full branding, incorporating logo on the front. Possibly also either a slogan e.g. "The Art of Cocktail Making' or details of the product e.g. "Cocktail Making Set' or similar.
• Outer white box - very simple design with logo to be displayed on the front of the packaging.
Should not have
• The design should not be too busy/complex. Not too much going on.

```html
<!DOCTYPE html>
<html lang="en">
<head>
<meta charset="utf-8">
<title>Shaker Haven – Cocktail Set Tube</title>
<link rel="preconnect" href="https://fonts.googleapis.com">
<link href="https://fonts.googleapis.com/css2?family=Pompiere&display=swap" rel="stylesheet">
<style>
  :root {
    --page-bg: #fdfdfd;
    --tube-black: #0f1013;
    --lid-rim: #b4b4b4;
    --lid-inner: #5e5e5e;
    --base-rim: #666666;
    --bubble-tint: #a9bccd;
    --text-white: #ffffff;
  }
  html, body {
    margin: 0;
    padding: 0;
    width: 729px;
    height: 1200px;
    overflow: hidden;
    background: var(--page-bg);
  }
  .canvas {
    display: block;
    width: 729px;
    height: 1200px;
  }
  .tube__base-rim { fill: var(--base-rim); }
  .tube__body { fill: var(--tube-black); }
  .tube__lid-rim { fill: var(--lid-rim); }
  .tube__lid-inner { fill: var(--lid-inner); }
  .bubble { fill: var(--bubble-tint); }
  .bubble--top { opacity: 0.17; }
  .bubble--middle { opacity: 0.2; }
  .bubble--bottom { opacity: 0.27; }
  .tagline,
  .feature-list {
    font-family: "Pompiere", "Arial Narrow", sans-serif;
    fill: var(--text-white);
  }
  .tagline { font-size: 30px; letter-spacing: 1px; }
  .feature-list { font-size: 23px; letter-spacing: 1px; }
</style>
</head>
<body>
<svg class="canvas" viewBox="0 0 729 1200" xmlns="http://www.w3.org/2000/svg" aria-label="Shaker Haven cocktail set tube">
  <defs>
    <clipPath id="tube-face">
      <rect x="164" y="141" width="401" height="943" rx="10"/>
    </clipPath>
  </defs>

  <ellipse class="tube__base-rim" cx="364" cy="1093" rx="193" ry="11"/>
  <rect class="tube__body" x="164" y="141" width="401" height="943" rx="10"/>

  <g class="bubbles" clip-path="url(#tube-face)">
    <ellipse class="bubble bubble--top" cx="471" cy="377" rx="110" ry="165"/>
    <ellipse class="bubble bubble--middle" cx="467" cy="651" rx="76" ry="230" transform="rotate(26 467 651)"/>
    <ellipse class="bubble bubble--bottom" cx="501" cy="908" rx="116" ry="143"/>
  </g>

  <ellipse class="tube__lid-rim" cx="364" cy="139" rx="196" ry="11"/>
  <ellipse class="tube__lid-inner" cx="364" cy="138" rx="180" ry="6"/>

  <text class="tagline" x="237" y="433" textLength="100" lengthAdjust="spacingAndGlyphs">The art of</text>
  <text class="tagline" x="187" y="470" textLength="150" lengthAdjust="spacingAndGlyphs">Cocktail Making</text>

  <text class="feature-list" x="198" y="518" textLength="139" lengthAdjust="spacingAndGlyphs">• FHSHSF DJDJM</text>
  <text class="feature-list" x="226" y="561" textLength="111" lengthAdjust="spacingAndGlyphs">• GSKS2SSDD</text>
  <text class="feature-list" x="183" y="604" textLength="154" lengthAdjust="spacingAndGlyphs">• FEMT - SSM D3"</text>
  <text class="feature-list" x="232" y="647" textLength="105" lengthAdjust="spacingAndGlyphs">• DNCACT 4"</text>
  <text class="feature-list" x="199" y="690" textLength="138" lengthAdjust="spacingAndGlyphs">• GNS E AFNNGG</text>
  <text class="feature-list" x="183" y="733" textLength="154" lengthAdjust="spacingAndGlyphs">• GN4S DDF V RRR</text>
  <text class="feature-list" x="198" y="774" textLength="139" lengthAdjust="spacingAndGlyphs">• FBASBC DAJGN</text>
</svg>
</body>
</html>
```